Maple Beacon Website

We are starting a marketing company and to do that we need a website! We want a website that will inspire and persuade to bring out the awesomeness in our clients.
What we want to see:
- Inspirational and persuasive imagery that relate to Branding.
- No cliche images eg. business man, suits and hand shakes
- We want to transform and educate our clients.
- We want to show them the path and would like our website to really act as a guide that guides them step by step through our process.
- We want the portray that we are an investment but not have a pretentious way to it. We put our heart into every project and that is how we treat our clients.
-When you submit your design please include what platform you have created for. Preference would be Wordpress or Joobla.

We have included the psd file for the wire frame, logo files, font files, site map and a link to a video we create to give you more information on what we would like to see. http://clipvault.example/t/qk82LmZpr

Feel free to make small modification to the logos if you think it will improve it. Your creativity and advice is most welcome.
Updates

One thing we forgot. We would like to have our contact information near the top of the website as well as at the bottom.  Here is out contact info:

Email: info@maplebeacon.example
Phone: 587-555-0142

Project Deadline Extended
Reason: As we are new with the platform and that we want to optimize our results, we decided to extend the deadline by 15 days. Thanks!

Target Market(s)

28-60, Male and Female, Oil field, Local Businesses, Dentists, Chiropractors, Hair salon, Construction/Renovation, Events etc

Industry/Entity Type

Investment

Requirements
Must have
• - 4 Inspirational and persuasive Imagery for the top portion of the website
- Must have a feel as if your not on a website an example of this is linked below.
http://www.artbidhub.example/design/402957/web-design-by-lena-torvik
Nice to have
• - Creative advice from you.
- Creative buttons for Get Free Quote and Subscribe buttons. Something out of the box that draws peoples attention. eg. a 'B' button. Just and example but still something related to branding.
Should not have
• No Cliches

```html
<!DOCTYPE html>
<html lang="en">
<head>
<meta charset="utf-8">
<title>Maple Beacon</title>
<link href="https://fonts.googleapis.com/css2?family=Cabin:ital,wght@0,400;0,600;0,700;1,400;1,600&family=PT+Sans:ital,wght@0,400;0,700;1,400&display=swap" rel="stylesheet">
<style>
  :root {
    --page: #fafafa;
    --green-dark: #5d7c38;
    --green-deep: #4f6d2a;
    --green-lime: #8caf2f;
    --green-button: #93b83a;
    --green-button-dark: #6f9420;
    --grey-tab: #a3a3a5;
    --grey-tab-dark: #8a8a8c;
    --grey-panel: #d8d8d8;
    --ink: #4a4a4a;
    --ink-soft: #5a5a5a;
    --card: #f5f5f5;
    --card-edge: #ebebeb;
    --field-edge: #c9c9c9;
    --footer: #4d4d4d;
    --white: #ffffff;
  }
  * { box-sizing: border-box; margin: 0; padding: 0; }
  html, body { width: 1200px; height: 981px; overflow: hidden; }
  body { background: var(--page); font-family: "PT Sans", sans-serif; color: var(--ink); position: relative; }
  .abs { position: absolute; }

  .brand { left: 130px; top: 34px; width: 220px; }
  .brand-name { display: flex; align-items: center; gap: 10px; font-family: "Cabin", sans-serif; font-weight: 700; font-size: 29px; color: #7d7d7f; line-height: 1; text-transform: uppercase; letter-spacing: 0.5px; }
  .brand-dot { width: 26px; height: 26px; background: var(--green-lime); border-radius: 50%; flex: none; }
  .brand-tagline { margin-top: 26px; text-align: center; font-family: "Cabin", sans-serif; font-style: italic; font-weight: 600; font-size: 15.5px; color: #5f5f5f; }

  .side-nav { left: 130px; top: 142px; width: 220px; height: 260px; background: var(--green-dark); border-radius: 4px; list-style: none; padding-top: 20px; }
  .side-nav li { height: 50px; padding-left: 44px; font-family: "Cabin", sans-serif; font-weight: 700; font-size: 15px; letter-spacing: 0.6px; color: var(--white); position: relative; line-height: 20px; }
  .side-nav li.current::before { content: ""; position: absolute; left: 18px; top: 5px; width: 10px; height: 10px; border-radius: 50%; background: #a8cc55; }

  .tab { top: 82px; width: 164px; height: 45px; border-radius: 4px 4px 0 0; background: linear-gradient(var(--grey-tab), var(--grey-tab-dark)); color: var(--white); font-family: "Cabin", sans-serif; font-weight: 700; font-size: 17px; text-align: center; line-height: 44px; text-shadow: 1px 1px 1px rgba(0,0,0,0.35); }
  .tab.active { background: linear-gradient(#6f9a33, #55782a); }
  .tab-pointer { left: 443px; top: 126px; width: 0; height: 0; border-left: 9px solid transparent; border-right: 9px solid transparent; border-top: 11px solid #55782a; z-index: 2; }

  .hero { left: 370px; top: 127px; width: 700px; height: 275px; border-radius: 0 0 4px 4px; background: linear-gradient(180deg, #e9e9e9 0%, #f1f1f1 55%, #dfe3da 75%, #e8ebe4 100%); overflow: hidden; }
  .hero-title { position: absolute; right: 17px; bottom: 10px; font-family: "Cabin", sans-serif; font-weight: 700; font-size: 48px; letter-spacing: 1px; color: var(--white); text-shadow: 2px 2px 3px rgba(0,0,0,0.45); }

  .panel { top: 422px; height: 98px; background: var(--grey-panel); box-shadow: 0 10px 10px -6px rgba(0,0,0,0.18); }
  .panel h2 { font-family: "Cabin", sans-serif; font-weight: 700; font-size: 19.5px; color: var(--ink); text-align: center; margin-top: 12px; letter-spacing: 0.3px; }
  .connect { left: 130px; width: 220px; }
  .social { display: flex; gap: 9px; margin: 14px 0 0 17px; list-style: none; }
  .social li { width: 30px; height: 30px; border-radius: 4px; }
  .newsletter { left: 371px; width: 699px; }
  .newsletter h2 span { color: var(--green-deep); }
  .news-field { left: 82px; top: 49px; width: 404px; height: 33px; background: var(--white); border: 1px solid var(--field-edge); border-radius: 5px; box-shadow: inset 0 2px 3px rgba(0,0,0,0.12); }

  .btn { background: linear-gradient(#a4c64a, var(--green-button-dark)); border: 1px solid #6a8c22; border-radius: 3px; color: var(--white); font-family: "Cabin", sans-serif; font-weight: 700; text-align: center; text-shadow: 1px 1px 1px rgba(0,0,0,0.35); }
  .btn-subscribe { left: 496px; top: 49px; width: 123px; height: 33px; font-size: 16px; line-height: 31px; letter-spacing: 0.5px; }

  .card { top: 554px; height: 320px; background: var(--card); border: 3px solid var(--card-edge); }
  .card h3 { font-family: "Cabin", sans-serif; font-weight: 700; font-size: 23px; color: var(--green-deep); }
  .welcome { left: 130px; width: 620px; padding: 12px 21px; }
  .lead { margin-top: 10px; color: var(--green-lime); font-weight: 700; font-size: 14.5px; line-height: 22px; }
  .body-copy { margin-top: 12px; color: var(--ink-soft); font-size: 13.5px; line-height: 23px; }
  .btn-read { left: 21px; top: 262px; width: 101px; height: 29px; font-size: 15px; line-height: 27px; }

  .quote { left: 770px; width: 300px; padding: 12px 19px; }
  .quote-intro { margin-top: 4px; font-style: italic; font-size: 12.5px; line-height: 15px; color: var(--ink-soft); }
  .field { left: 20px; width: 252px; height: 26px; background: var(--white); border: 1px solid var(--field-edge); border-radius: 3px; box-shadow: inset 0 1px 3px rgba(0,0,0,0.1); font-style: italic; font-size: 11.5px; color: #9a9a9a; padding: 6px 13px; }
  .field.comments { height: 58px; }
  .btn-submit { left: 171px; top: 279px; width: 101px; height: 29px; font-size: 15px; line-height: 27px; }

  .site-footer { left: 0; top: 892px; width: 1200px; height: 89px; background: var(--footer); text-align: center; color: var(--white); }
  .footer-nav { list-style: none; display: flex; justify-content: center; margin-top: 24px; font-size: 11px; letter-spacing: 0.4px; }
  .footer-nav li + li::before { content: "|"; margin: 0 13px; }
  .copyright { margin-top: 8px; font-size: 10.5px; letter-spacing: 0.4px; color: #d0d0d0; }
</style>
</head>
<body>
  <header class="brand abs">
    <div class="brand-name"><span class="brand-dot"></span>Maple Beacon</div>
    <p class="brand-tagline">Because You´re Awesome!</p>
  </header>

  <ul class="side-nav abs">
    <li class="current">STRATEGY</li>
    <li>PORTFOLIO</li>
    <li>ABOUT US</li>
    <li>CONTACT US</li>
    <li>BLOG</li>
  </ul>

  <div class="tab active abs" style="left:370px">Maple Beacon</div>
  <div class="tab abs" style="left:549px">Be Found</div>
  <div class="tab abs" style="left:728px">Connect</div>
  <div class="tab abs" style="left:906px">Get Growing</div>
  <div class="tab-pointer abs"></div>

  <section class="hero abs" role="img" aria-label="Row of green apples on a white table with a hand reaching for the one red apple">
    <div class="hero-title">MAPLE BEACON</div>
  </section>

  <section class="panel connect abs">
    <h2>CONNECT WITH US</h2>
    <ul class="social">
      <li style="background:#3b5a9a"></li>
      <li style="background:#6cc7e6"></li>
      <li style="background:#2a7bb0"></li>
      <li style="background:#f47d20"></li>
      <li style="background:#d02a24"></li>
    </ul>
  </section>

  <section class="panel newsletter abs">
    <h2>GET TIPS AND TRICKS! <span>SUBSCRIBE TO OUR NEWSLETTER</span></h2>
    <div class="news-field abs"></div>
    <div class="btn btn-subscribe abs">SUBSCRIBE</div>
  </section>

  <section class="card welcome abs">
    <h3>Welcome to Our Site</h3>
    <p class="lead">Lorem ipsum dolor sit amet, consectetur adipiscing elit. Fusce accumsan, elit a suscipit sagittis, tortor sapien cursus risus, non rhoncus lectus nunc ac nulla..</p>
    <p class="body-copy">Aliquam molestie, mi et imperdiet euismod, dui purus auctor tellus, et interdum lacus lectus et ante. Sed accumsan sollicitudin sapien, sit amet adipiscing turpis gravida ac. In congue, neque ac lobortis volutpat, libero mauris varius mi, vitae suscipit ipsum ligula vitae risus. Duis aliquam nibh a dui iaculis viverra id a velit. Vivamus egestas risus in magna varius commodo. Sed semper viverra egestas. Etiam pretium porttitor lectus, vel ornare neque porta volutpat. Aenean a nibh eget turpis vehicula tempus ac sed massa.</p>
    <div class="btn btn-read abs">Read More</div>
  </section>

  <section class="card quote abs">
    <h3>Get a Free Quote</h3>
    <p class="quote-intro">If you would like to more information on how we can help you achive your goals. You can visit our strategy page or simply get a free Quote !</p>
    <div class="field abs" style="top:106px">Full Name</div>
    <div class="field abs" style="top:142px">Email Address</div>
    <div class="field abs" style="top:177px">Contact No.</div>
    <div class="field comments abs" style="top:213px">Comments</div>
    <div class="btn btn-submit abs">Submit Now</div>
  </section>

  <footer class="site-footer abs">
    <ul class="footer-nav">
      <li>STRATEGY</li><li>PORTFOLIO</li><li>ABOUT US</li><li>CONTACT US</li><li>BLOG</li><li>SITE MAP</li>
    </ul>
    <p class="copyright">COPYRIGHT ©2013. MAPLE BEACON INC. | ALL RIGHT RESERVED</p>
  </footer>
</body>
</html>
```